Cocktail-Making Assistant App re-design

Ok boys and girls, here's the deal:
I have an android app which is almost complete, but needs a design overhaul.

The app is a standard cocktail-making assistant: gives you a list of cocktails and the ability to see which cocktail you can make out of those ingredients (drinks, fruit, etc) you have at home.

I've attached some general app flow, as well as detailed requirements/explanation presentation. Most of those things are just FYI, so that you know what it's about.

3 screens are the most important (main screen, cocktail view screen, ingredient view screen), meaning I will pick the design mostly based on ideas for those 3 things, with the fourth being a rather simple list (given on attached flow, third tier)
Some other screens are derived from that, with some minor changes on it, but you shouldn't care about that.

There are lots of other, non-explained things which I said nothing about only because they are (from design point of view) completely the same and would only make it seem more complicated.

I don't want to influence the colour scheme, but the app will be released under RedFig developer name (having a light colured red fig as a logo) so I suppose some brownish design, for example, will not really fit nicely. If you, however, have a killer which you are confident will prove me wrong, I'm looking forward to seeing it!

It should be a serious, elegant look (as opposed to cartoonish, but we are not aiming for a business look at all!), not cluttered with details, no clubbing themes, glitter and so on.

Test apk file available on request (Android 2.3+).

Edit: payment is now guaranteed
Also please note that currently, the favorite, "heart" button has a motion effect:
on click it flies out of the screen to the left (white heart) and comes back to the screen as a red heart. Take that into consideration, if it means anything to you.

Target Market(s)

Whoever you imagine would enjoy drinking cocktails

Industry/Entity Type

Business

Requirements
Must have
• Everything is said in the provided documentation - images say more than I could possibly write here.
Nice to have
• As said, most of the icons are a nice-to-have. Only those which are critically linked to the rest of the design must be provided. More details in the docs.
Should not have
• No cartoon look, No zillion colours

```html
<!DOCTYPE html>
<html lang="en">
<head>
<meta charset="utf-8">
<title>Cocktail Search</title>
<link rel="stylesheet" href="https://fonts.googleapis.com/css2?family=Michroma&display=swap">
<style>
:root{
  --bg:#f4f4f4;
  --card:#f7f7f7;
  --line:#cfcfcf;
  --ink:#111111;
  --accent:#d8232f;
  --accent-dark:#a5141d;
  --search:#dddbe0;
  --search-text:#7d7b80;
  --star-green:#93d36c;
  --star-orange:#f6a840;
  --star-red:#ef4b5a;
  --star-lilac:#b7a7e8;
  --star-tan:#cbb1a9;
  --star-off:#2b2b2b;
}
*{box-sizing:border-box;margin:0;padding:0}
html,body{width:676px;height:1200px;overflow:hidden;background:var(--bg)}
body{font-family:"Michroma",sans-serif;color:var(--ink);position:relative}
.app-header{position:absolute;left:0;top:0;width:676px;height:97px;background:linear-gradient(#ffffff,#f2f2f2)}
.back-home{position:absolute;left:10px;top:22px;display:flex;align-items:center;gap:2px}
.header-divider{position:absolute;left:131px;top:14px;width:1px;height:72px;background:#dcdcdc}
.screen-title{position:absolute;left:164px;top:36px;font-size:25px;font-weight:400;letter-spacing:2px;white-space:nowrap}
.accent-band{position:absolute;left:0;top:97px;width:676px;height:10px;background:linear-gradient(var(--accent),var(--accent-dark))}
.search-area{position:absolute;left:0;top:107px;width:676px;height:75px;background:var(--bg);border-bottom:1px solid var(--line)}
.search-field{position:absolute;left:65px;top:11px;width:544px;height:39px;border-radius:20px;background:var(--search);display:flex;align-items:center}
.search-label{margin-left:116px;font-size:18px;letter-spacing:2px;color:var(--search-text)}
.search-icon{position:absolute;right:38px;top:6px}
.cocktail-grid{position:absolute;left:0;top:182px;width:676px;height:1018px;display:grid;grid-template-columns:339px 337px;grid-template-rows:338px 338px 342px}
.cocktail-card{position:relative;background:var(--card);border-right:1px solid var(--line);border-bottom:1px solid var(--line);overflow:hidden}
.cocktail-card:nth-child(2n){border-right:none}
.drink-photo{position:absolute;top:35px;left:105px;width:96px;height:180px;border-radius:8px}
.stock{position:absolute;top:30px;left:228px;width:92px;text-align:center;font-size:15px;line-height:23px;letter-spacing:1px}
.stock svg{display:block;margin:0 auto 4px}
.drink-name{position:absolute;top:250px;font-size:20px;font-weight:400;line-height:30px;letter-spacing:1px;white-space:nowrap}
.rating{position:absolute;top:294px;display:flex;gap:7px}
.rating svg{width:31px;height:30px}
.s-green{fill:var(--star-green)}.s-orange{fill:var(--star-orange)}.s-red{fill:var(--star-red)}
.s-lilac{fill:var(--star-lilac)}.s-tan{fill:var(--star-tan)}.s-off{fill:var(--star-off)}
</style>
</head>
<body>
<svg width="0" height="0" style="position:absolute">
  <defs>
    <symbol id="star" viewBox="0 0 24 24"><path d="M12 1.5l3.1 7 7.4.6-5.6 4.9 1.7 7.3L12 17.4l-6.6 3.9 1.7-7.3L1.5 9.1l7.4-.6z"/></symbol>
    <symbol id="shaker" viewBox="0 0 26 42"><path d="M10 0h6v3h-6z M6 4h14l1 8H5z M4 13h18l-2 29H6z" fill="#222"/></symbol>
  </defs>
</svg>

<header class="app-header">
  <div class="back-home">
    <svg width="20" height="30" viewBox="0 0 20 30"><path d="M16 5L5 15l11 10" fill="none" stroke="var(--accent)" stroke-width="3"/></svg>
    <svg width="56" height="52" viewBox="0 0 56 52"><path d="M28 2L2 26h8v24h14V34h8v16h14V26h8L42 13V4h-7v3z" fill="var(--ink)"/></svg>
  </div>
  <div class="header-divider"></div>
  <h1 class="screen-title">COCKTAIL SEARCH</h1>
</header>
<div class="accent-band"></div>

<div class="search-area">
  <div class="search-field">
    <span class="search-label">SEARCH ALL</span>
    <svg class="search-icon" width="28" height="28" viewBox="0 0 28 28"><circle cx="11" cy="11" r="8" fill="none" stroke="#222" stroke-width="3"/><path d="M17 17l9 9" stroke="#222" stroke-width="4.5" stroke-linecap="round"/></svg>
  </div>
</div>

<main class="cocktail-grid">
  <article class="cocktail-card">
    <div class="drink-photo" role="img" aria-label="Tulip tasting glass with golden drink" style="background:linear-gradient(#eef0f0 0%,#f3f1ea 45%,#e6d38a 60%,#e9e7e0 80%,#dcdcdc 100%)"></div>
    <div class="stock"><svg width="26" height="42"><use href="#shaker"/></svg>HAVE<br>0 OF 8</div>
    <h2 class="drink-name" style="left:61px">'57 ROADSTER</h2>
    <div class="rating" style="left:67px"><svg class="s-green"><use href="#star"/></svg><svg class="s-orange"><use href="#star"/></svg><svg class="s-red"><use href="#star"/></svg><svg class="s-lilac"><use href="#star"/></svg><svg class="s-tan"><use href="#star"/></svg></div>
  </article>

  <article class="cocktail-card">
    <div class="drink-photo" role="img" aria-label="Pint glass with pink red drink" style="left:90px;width:108px;background:linear-gradient(#f3dfe2 0%,#ec5a70 15%,#e9425a 70%,#f2c9cf 100%)"></div>
    <div class="stock"><svg width="26" height="42"><use href="#shaker"/></svg>HAVE<br>0 OF 5</div>
    <h2 class="drink-name" style="left:42px">'57 ROADSTER #2</h2>
    <div class="rating" style="left:54px"><svg class="s-green"><use href="#star"/></svg><svg class="s-orange"><use href="#star"/></svg><svg class="s-red"><use href="#star"/></svg><svg class="s-lilac"><use href="#star"/></svg><svg class="s-off"><use href="#star"/></svg></div>
  </article>

  <article class="cocktail-card">
    <div class="drink-photo" role="img" aria-label="Wine glass with red drink and strawberry garnish" style="left:112px;width:78px;background:linear-gradient(#e56070 0%,#c8162a 45%,#eeeeee 62%,#e2e2e2 100%)"></div>
    <div class="stock"><svg width="26" height="42"><use href="#shaker"/></svg>HAVE<br>0 OF 6</div>
    <h2 class="drink-name" style="left:40px;top:220px">'57 ROADSTER<br>WITH A WHITE<br>LICENSE PLATE</h2>
  </article>

  <article class="cocktail-card">
    <div class="drink-photo" role="img" aria-label="Rocks glass with green mint drink" style="left:94px;width:100px;top:40px;height:170px;background:linear-gradient(#4c8a3a 0%,#b7d24a 25%,#9fc23a 80%,#e9efe0 100%)"></div>
    <div class="stock"><svg width="26" height="42"><use href="#shaker"/></svg>HAVE<br>0 OF 4</div>
    <h2 class="drink-name" style="left:22px;top:232px">1-900-FUK-MEUP</h2>
    <div class="rating" style="left:54px;top:288px"><svg class="s-green"><use href="#star"/></svg><svg class="s-off"><use href="#star"/></svg><svg class="s-off"><use href="#star"/></svg><svg class="s-off"><use href="#star"/></svg><svg class="s-off"><use href="#star"/></svg></div>
  </article>

  <article class="cocktail-card">
    <div class="drink-photo" role="img" aria-label="Highball glass with bright blue drink and lime" style="left:128px;width:80px;top:42px;height:170px;background:linear-gradient(#bfe8f5 0%,#25b6e8 25%,#1a9fd8 85%,#e6eef0 100%)"></div>
    <div class="stock"><svg width="26" height="42"><use href="#shaker"/></svg>HAVE<br>0 OF 4</div>
    <h2 class="drink-name" style="left:24px;top:232px">110 IN THE SHADE</h2>
    <div class="rating" style="left:88px;top:291px"><svg class="s-green"><use href="#star"/></svg><svg class="s-orange"><use href="#star"/></svg><svg class="s-red"><use href="#star"/></svg><svg class="s-off"><use href="#star"/></svg><svg class="s-off"><use href="#star"/></svg></div>
  </article>

  <article class="cocktail-card">
    <div class="drink-photo" role="img" aria-label="Pint glass with amber drink" style="left:90px;width:108px;top:30px;height:182px;background:linear-gradient(#f2ecd8 0%,#eac05a 12%,#e2a838 80%,#ece5d2 100%)"></div>
    <div class="stock"><svg width="26" height="42"><use href="#shaker"/></svg>HAVE<br>0 OF 8</div>
    <h2 class="drink-name" style="left:33px;top:232px">151 FLORIDA<br>BUSHWACKER</h2>
  </article>
</main>
</body>
</html>
```